Talvique Hotels Business Card and Logo

We need a business card design for a hotel group. I saw a hotel card you designed and really liked it. We have multiple properties with different brands. Were hoping that the card would be unique and find a way to list out all our properties. Our web address is www.talviquehotels.com. I have attached some photos of card designs I like.

Industry/Entity Type

Hotel

Contact Information for Business Card

Scott CurranReneson HotelsChief Operating Officer56 Madera DriveCorte Madera, CA 94925Office 415-891-5013Cell 707-5550143

```html
<!DOCTYPE html>
<html lang="en">
<head>
<meta charset="utf-8">
<title>Talvique Hotels – Business Card Colourways</title>
<link rel="stylesheet" href="https://fonts.googleapis.com/css2?family=Lobster&family=PT+Sans:wght@400;700&display=swap">
<style>
  :root {
    --backdrop: #000000;
    --card: #ffffff;
    --olive: #7d6e0f;
    --coral: #f0562d;
    --teal: #12aaa0;
    --bark: #5a3a22;
    --ochre: #d08a33;
    --wine: #7a1e2d;
    --stone: #9a9a9a;
  }
  * { margin: 0; padding: 0; box-sizing: border-box; }
  html, body {
    width: 1200px; height: 892px; overflow: hidden;
    background: var(--backdrop);
  }
  .sheet { position: relative; width: 1200px; height: 892px; }

  .card {
    position: absolute; width: 331px; height: 184px;
    background: var(--card); overflow: hidden;
    font-family: "PT Sans", Arial, sans-serif;
  }
  .card--olive { left: 167px; top: 164px; --rule: var(--olive); --accent: var(--coral); --detail: var(--olive); }
  .card--teal  { left: 734px; top: 164px; --rule: var(--teal);  --accent: var(--bark);  --detail: var(--teal); }
  .card--ochre { left: 167px; top: 556px; --rule: var(--ochre); --accent: var(--wine);  --detail: var(--ochre); }
  .card--stone { left: 734px; top: 556px; --rule: var(--stone); --accent: var(--wine);  --detail: var(--stone); }

  .rule { position: absolute; top: 79px; height: 4px; background: var(--rule); }
  .rule--left  { left: 0; width: 44px; }
  .rule--right { left: 128px; right: 0; }

  .brand-ring {
    position: absolute; left: 44px; top: 23px; width: 84px; height: 84px;
    border: 4px solid var(--rule); border-radius: 50%;
    display: flex; align-items: center; justify-content: center;
    text-align: center;
  }
  .brand-name {
    font-weight: 700; font-size: 11px; line-height: 1.15; color: var(--accent);
  }

  .holder { position: absolute; left: 159px; top: 25px; }
  .holder-name {
    font-family: "Lobster", cursive; font-weight: 400; font-size: 16px; line-height: 1;
    color: var(--accent); white-space: nowrap;
  }
  .holder-title {
    margin-top: 4px; font-size: 10.5px; color: var(--accent); white-space: nowrap;
  }

  .contact { position: absolute; left: 20px; top: 126px; list-style: none; }
  .contact-row {
    display: flex; align-items: center; height: 15.5px;
    font-size: 8.5px; color: var(--detail); white-space: nowrap;
  }
  .contact-icon { width: 11px; height: 11px; margin-right: 7px; flex: none; }
  .contact-icon circle { fill: var(--accent); }
  .contact-icon path { fill: #ffffff; }
</style>
</head>
<body>
<main class="sheet">

  <section class="card card--olive">
    <div class="rule rule--left"></div><div class="rule rule--right"></div>
    <div class="brand-ring"><span class="brand-name">Talvique<br>Hotels</span></div>
    <header class="holder">
      <h1 class="holder-name">Brent Holloway Talvique</h1>
      <p class="holder-title">HotelsChief Operating Officer</p>
    </header>
    <ul class="contact">
      <li class="contact-row"><svg class="contact-icon" viewBox="0 0 12 12"><circle cx="6" cy="6" r="6"/><path d="M6 2.5a2.2 2.2 0 0 0-2.2 2.2C3.8 6.4 6 9.5 6 9.5s2.2-3.1 2.2-4.8A2.2 2.2 0 0 0 6 2.5zm0 3.1a.9.9 0 1 1 0-1.8.9.9 0 0 1 0 1.8z"/></svg>83 Pellwick LaneBrindle Cove, NV 89317</li>
      <li class="contact-row"><svg class="contact-icon" viewBox="0 0 12 12"><circle cx="6" cy="6" r="6"/><path d="M4.1 2.8l1 1.6-.6.7a4.6 4.6 0 0 0 2.4 2.4l.7-.6 1.6 1-.5 1.1C6.2 9 3 5.8 3 3.3z"/></svg>Office 0186-555-318</li>
      <li class="contact-row"><svg class="contact-icon" viewBox="0 0 12 12"><circle cx="6" cy="6" r="6"/><path d="M4.1 2.8l1 1.6-.6.7a4.6 4.6 0 0 0 2.4 2.4l.7-.6 1.6 1-.5 1.1C6.2 9 3 5.8 3 3.3z"/></svg>Cell 5550143-662</li>
    </ul>
  </section>

  <section class="card card--teal">
    <div class="rule rule--left"></div><div class="rule rule--right"></div>
    <div class="brand-ring"><span class="brand-name">Talvique<br>Hotels</span></div>
    <header class="holder">
      <h1 class="holder-name">Brent Holloway Talvique</h1>
      <p class="holder-title">HotelsChief Operating Officer</p>
    </header>
    <ul class="contact">
      <li class="contact-row"><svg class="contact-icon" viewBox="0 0 12 12"><circle cx="6" cy="6" r="6"/><path d="M6 2.5a2.2 2.2 0 0 0-2.2 2.2C3.8 6.4 6 9.5 6 9.5s2.2-3.1 2.2-4.8A2.2 2.2 0 0 0 6 2.5zm0 3.1a.9.9 0 1 1 0-1.8.9.9 0 0 1 0 1.8z"/></svg>83 Pellwick LaneBrindle Cove, NV 89317</li>
      <li class="contact-row"><svg class="contact-icon" viewBox="0 0 12 12"><circle cx="6" cy="6" r="6"/><path d="M4.1 2.8l1 1.6-.6.7a4.6 4.6 0 0 0 2.4 2.4l.7-.6 1.6 1-.5 1.1C6.2 9 3 5.8 3 3.3z"/></svg>Office 0186-555-318</li>
      <li class="contact-row"><svg class="contact-icon" viewBox="0 0 12 12"><circle cx="6" cy="6" r="6"/><path d="M4.1 2.8l1 1.6-.6.7a4.6 4.6 0 0 0 2.4 2.4l.7-.6 1.6 1-.5 1.1C6.2 9 3 5.8 3 3.3z"/></svg>Cell 5550143-662</li>
    </ul>
  </section>

  <section class="card card--ochre">
    <div class="rule rule--left"></div><div class="rule rule--right"></div>
    <div class="brand-ring"><span class="brand-name">Talvique<br>Hotels</span></div>
    <header class="holder">
      <h1 class="holder-name">Brent Holloway Talvique</h1>
      <p class="holder-title">HotelsChief Operating Officer</p>
    </header>
    <ul class="contact">
      <li class="contact-row"><svg class="contact-icon" viewBox="0 0 12 12"><circle cx="6" cy="6" r="6"/><path d="M6 2.5a2.2 2.2 0 0 0-2.2 2.2C3.8 6.4 6 9.5 6 9.5s2.2-3.1 2.2-4.8A2.2 2.2 0 0 0 6 2.5zm0 3.1a.9.9 0 1 1 0-1.8.9.9 0 0 1 0 1.8z"/></svg>83 Pellwick LaneBrindle Cove, NV 89317</li>
      <li class="contact-row"><svg class="contact-icon" viewBox="0 0 12 12"><circle cx="6" cy="6" r="6"/><path d="M4.1 2.8l1 1.6-.6.7a4.6 4.6 0 0 0 2.4 2.4l.7-.6 1.6 1-.5 1.1C6.2 9 3 5.8 3 3.3z"/></svg>Office 0186-555-318</li>
      <li class="contact-row"><svg class="contact-icon" viewBox="0 0 12 12"><circle cx="6" cy="6" r="6"/><path d="M4.1 2.8l1 1.6-.6.7a4.6 4.6 0 0 0 2.4 2.4l.7-.6 1.6 1-.5 1.1C6.2 9 3 5.8 3 3.3z"/></svg>Cell 5550143-662</li>
    </ul>
  </section>

  <section class="card card--stone">
    <div class="rule rule--left"></div><div class="rule rule--right"></div>
    <div class="brand-ring"><span class="brand-name">Talvique<br>Hotels</span></div>
    <header class="holder">
      <h1 class="holder-name">Brent Holloway Talvique</h1>
      <p class="holder-title">HotelsChief Operating Officer</p>
    </header>
    <ul class="contact">
      <li class="contact-row"><svg class="contact-icon" viewBox="0 0 12 12"><circle cx="6" cy="6" r="6"/><path d="M6 2.5a2.2 2.2 0 0 0-2.2 2.2C3.8 6.4 6 9.5 6 9.5s2.2-3.1 2.2-4.8A2.2 2.2 0 0 0 6 2.5zm0 3.1a.9.9 0 1 1 0-1.8.9.9 0 0 1 0 1.8z"/></svg>83 Pellwick LaneBrindle Cove, NV 89317</li>
      <li class="contact-row"><svg class="contact-icon" viewBox="0 0 12 12"><circle cx="6" cy="6" r="6"/><path d="M4.1 2.8l1 1.6-.6.7a4.6 4.6 0 0 0 2.4 2.4l.7-.6 1.6 1-.5 1.1C6.2 9 3 5.8 3 3.3z"/></svg>Office 0186-555-318</li>
      <li class="contact-row"><svg class="contact-icon" viewBox="0 0 12 12"><circle cx="6" cy="6" r="6"/><path d="M4.1 2.8l1 1.6-.6.7a4.6 4.6 0 0 0 2.4 2.4l.7-.6 1.6 1-.5 1.1C6.2 9 3 5.8 3 3.3z"/></svg>Cell 5550143-662</li>
    </ul>
  </section>

</main>
</body>
</html>
```